Highlight Document Over Image for Slide

We are seeking a graphic designer to overlay a news article on an image that pertains to the article, aiming for a stylish yet professional appearance. Given the limited resources, we encourage you to use your imagination and go beyond what basic tools like PowerPoint can offer.

```html
<!DOCTYPE html>
<html lang="en">
<head>
<meta charset="utf-8">
<title>Rule 20 – Introduction or Possession of Contraband Items</title>
<link rel="stylesheet" href="https://fonts.googleapis.com/css2?family=Arimo:wght@400;700&display=swap">
<style>
  :root {
    --page: #ffffff;
    --band: #4a4a4a;
    --frame: #111111;
    --panel: rgba(38, 38, 38, 0.9);
    --ink-light: #ffffff;
    --aerial-dry: #9c8a66;
    --aerial-built: #6f6a63;
    --aerial-water: #6b6b62;
  }
  * { margin: 0; padding: 0; box-sizing: border-box; }
  html, body { width: 1200px; height: 772px; overflow: hidden; background: var(--page); }
  .slide {
    position: relative;
    width: 1200px;
    height: 772px;
    background: var(--page);
    font-family: "Arimo", Arial, sans-serif;
    color: var(--ink-light);
  }
  .side-band {
    position: absolute;
    left: 747px; top: 0;
    width: 453px; height: 772px;
    background: var(--band);
  }
  .slide-frame {
    position: absolute;
    left: 54px; top: 54px;
    width: 1094px; height: 671px;
    border: 2px solid var(--frame);
  }
  .site-aerial {
    position: absolute;
    left: 91px; top: 90px;
    width: 1018px; height: 596px;
    background:
      radial-gradient(ellipse 45% 40% at 55% 55%, var(--aerial-built) 0%, transparent 70%),
      linear-gradient(175deg, var(--aerial-dry) 0%, #8a7b5e 30%, var(--aerial-built) 55%, var(--aerial-water) 80%, #5f6058 100%);
  }
  .rule-panel {
    position: absolute;
    left: 747px; top: 90px;
    width: 362px; height: 596px;
    background: var(--panel);
  }
  .rule-number {
    position: absolute;
    left: 779px; top: 116px;
    font-size: 92px;
    font-weight: 700;
    line-height: 1;
    letter-spacing: -3px;
  }
  .rule-title {
    position: absolute;
    left: 886px; top: 123px;
    font-size: 20.5px;
    font-weight: 700;
    line-height: 24.5px;
    text-transform: uppercase;
  }
  .rule-body {
    position: absolute;
    left: 780px; top: 213px;
    width: 330px;
    font-size: 19.4px;
    line-height: 24px;
  }
  .rule-body p + p { margin-top: 24px; }
  .page-number {
    position: absolute;
    left: 1109px; top: 692px;
    font-size: 19px;
    color: var(--ink-light);
  }
</style>
</head>
<body>
<main class="slide">
  <div class="side-band"></div>
  <div class="slide-frame"></div>
  <div class="site-aerial" role="img" aria-label="Aerial map view of a waterfront correctional facility with roads, buildings and bay shoreline"></div>
  <div class="rule-panel"></div>
  <div class="rule-number">20</div>
  <h1 class="rule-title">Introduction or<br>Possession of<br>Contraband Items</h1>
  <div class="rule-body">
    <p>Employees shall not introduce or<br>possess unauthorized items such<br>as escape paraphernalia, weapons,<br>facsimiles of weapons, ammunition,<br>wireless communication devices,<br>cell phones, tobacco or facsimiles<br>of tobacco products<br>(e.g. electronic vapor cigarettes),<br>lighters or any other item not<br>specifically authorized by PD<br>04.04.100 "Custody, Security and<br>Safety Systems (Exempt)", OP<br>04.04.100 "Gate Security" or facility<br>operating procedure in any facility<br>where offenders are housed.</p>
    <p>Employees are responsible for any<br>item in their</p>
  </div>
  <div class="page-number">36</div>
</main>
</body>
</html>
```